Banner Ad in Spanish for Car Accident Law Firm in Miami Florida

I need a Banner Ad in Spanish Language. We are an Accident Law Firm in Miami, FL. We help injured people. I need a Banner Ad with a Vibrant Colorful Background to Stand Out. A Click-Able Call to Action is needed. We don't want to make the banner too crowded and we want the message to be simple to understand. We are looking for a skilled graphic designer to create a visually appealing banner ad for our YouTube marketing campaign. The required dimensions and format are:
1920 x 275
.png & .mp4

The Banner is for our Plaintiff’s Personal Injury Law Firm. We represent Spanish Speaking clients who are injured in CAR ACCIDENTS. As such the banner must include:
1. Our Firm Logo
2. Our Telephone# (305) 447-2086
3. Stock Photo of Car Crash
4. Photo of our attorney in office
5. The Words Abogados de Accidentes
The telephone number should be fairly large and stand out it is our call to action. The words Abogados de Accidentes should be close to our Logo to associate the two.

Target Market(s)

Car Accident Victims who speak Spanish

Industry/Entity Type

Legal, Law Firm.

Font styles to use
Sans Serif

Colors
59FF00
82FF00
B8FF75
E3FFCB
F4FFEA
F0912C
F2A743
F7CA91
FBE8D2
FDF5EE
6B429C
8869AF
B7A5CE
E3DAEB
F3F0F8

Requirements
Must have
• A bold background so that Banner Ad can be seen on mobile and against the screen being advertising against
Should not have
• Be too crowded. Hard to understand what it is for.

```html
<!DOCTYPE html>
<html lang="es">
<head>
<meta charset="utf-8">
<title>Solaria Law Firm – Abogados de Accidentes</title>
<link href="https://fonts.googleapis.com/css2?family=Oswald:wght@500;600;700&display=swap" rel="stylesheet">
<style>
  :root {
    --page: #dedede;
    --purple-top: #a57cc8;
    --purple-mid: #6b429c;
    --purple-deep: #3b1770;
    --orange-light: #f7c27a;
    --orange: #f0912c;
    --orange-deep: #e4661a;
    --crash-red: #b3202a;
    --crash-dark: #3a1a1c;
    --accent-purple: #6b429c;
    --white: #ffffff;
  }
  html, body {
    margin: 0;
    padding: 0;
    width: 1200px;
    height: 286px;
    overflow: hidden;
    background: var(--page);
  }
  .canvas {
    position: relative;
    width: 1200px;
    height: 286px;
    font-family: "Oswald", sans-serif;
  }
  .banner {
    position: absolute;
    left: 52px;
    top: 64px;
    width: 1097px;
    height: 157px;
    overflow: hidden;
    background: var(--purple-mid);
  }
  .banner__edge {
    position: absolute;
    left: 0; top: 0;
    width: 3px; height: 100%;
    background: var(--orange);
    z-index: 2;
  }
  .banner__city {
    position: absolute;
    left: 0; top: 0;
    width: 615px; height: 100%;
    background: linear-gradient(180deg, var(--purple-top) 0%, var(--purple-mid) 45%, var(--purple-deep) 100%);
  }
  .banner__crash {
    position: absolute;
    left: 615px; top: 0;
    right: 0; height: 100%;
    background: linear-gradient(180deg, var(--orange-light) 0%, var(--orange) 50%, var(--orange-deep) 100%);
  }
  .crash-photo {
    position: absolute;
    left: 884px;
    top: 7px;
    width: 192px;
    height: 150px;
    border-radius: 22px 22px 0 22px;
    background: linear-gradient(135deg, var(--crash-dark) 0%, var(--crash-red) 45%, #d23a30 65%, var(--crash-dark) 100%);
  }
  .banner__corner {
    position: absolute;
    right: 0; bottom: 0;
    z-index: 1;
  }
  .brand {
    position: absolute;
    left: 39px;
    top: 36px;
    display: flex;
    align-items: center;
    gap: 8px;
    color: var(--white);
  }
  .brand__mark {
    width: 14px;
    height: 14px;
    background: var(--white);
    border-radius: 3px;
  }
  .brand__name {
    font-weight: 500;
    font-size: 22px;
    letter-spacing: 1px;
    line-height: 1;
  }
  .brand__sub {
    display: block;
    font-size: 9px;
    letter-spacing: 1.5px;
    text-align: right;
    margin-top: 2px;
  }
  .headline {
    position: absolute;
    left: 282px;
    top: 28px;
    margin: 0;
    color: var(--white);
    font-weight: 700;
    font-size: 39px;
    line-height: 45px;
    letter-spacing: 0.5px;
    text-transform: uppercase;
  }
  .attorney {
    position: absolute;
    left: 545px;
    top: 9px;
    width: 132px;
    height: 148px;
    background: linear-gradient(180deg, #c8b6a6 0%, #9a9ea6 45%, #7d828a 100%);
    border-radius: 50px 50px 0 0;
  }
  .cta {
    position: absolute;
    left: 703px;
    top: 59px;
    width: 160px;
    height: 40px;
    background: var(--white);
    border-radius: 20px 20px 0 20px;
    display: flex;
    align-items: center;
    justify-content: center;
    gap: 6px;
    color: var(--orange);
    font-weight: 600;
    font-size: 17px;
    letter-spacing: 0.2px;
    text-decoration: none;
    z-index: 2;
  }
  .cta svg { width: 12px; height: 12px; fill: var(--orange); }
</style>
</head>
<body>
<div class="canvas">
  <div class="banner">
    <div class="banner__city" role="img" aria-label="Purple-tinted city skyline photo"></div>
    <div class="banner__crash" role="img" aria-label="Orange-tinted photo of a car crash"></div>
    <div class="crash-photo" role="img" aria-label="Close-up photo of a wrecked red car"></div>
    <svg class="banner__corner" width="70" height="68" viewBox="0 0 70 68" aria-hidden="true">
      <polygon points="70,0 70,68 0,68" fill="var(--accent-purple)"/>
    </svg>
    <div class="banner__edge"></div>

    <div class="brand">
      <span class="brand__mark"></span>
      <span class="brand__name">SOLARIA<span class="brand__sub">LAW FIRM</span></span>
    </div>

    <h1 class="headline">Abogados de<br>Accidentes</h1>

    <div class="attorney" role="img" aria-label="Photo of the firm's attorney in a grey suit"></div>

    <a class="cta" href="tel:+13054472086">
      <svg viewBox="0 0 24 24" aria-hidden="true"><path d="M6.6 10.8a15.1 15.1 0 0 0 6.6 6.6l2.2-2.2a1 1 0 0 1 1-.25 11.4 11.4 0 0 0 3.6.57 1 1 0 0 1 1 1V20a1 1 0 0 1-1 1A17 17 0 0 1 3 4a1 1 0 0 1 1-1h3.5a1 1 0 0 1 1 1c0 1.25.2 2.45.57 3.6a1 1 0 0 1-.25 1z"/></svg>
      (305) 447-2086
    </a>
  </div>
</div>
</body>
</html>
```